Cove medical spa and wellness

Integrate existing logo and web design (colors and background) into tri fold, single card brochure and business card design. We already have a logo and an idea for our promotional material but we would like someone to bring it together for us! Covewellnessandspa.com. We want to see what a marble background with a faded lily (as seen on our webpage) would look like on brochures and business cards.

```html
<!DOCTYPE html>
<html lang="en">
<head>
<meta charset="utf-8">
<title>Cove Medical Spa &amp; Wellness – Business Card</title>
<link href="https://fonts.googleapis.com/css2?family=Dancing+Script:wght@700&family=Poppins:wght@400;500&display=swap" rel="stylesheet">
<style>
  :root {
    --page-bg: #e6e4e0;
    --card-bg: #2b2b2b;
    --gold: #c9a233;
    --gold-soft: rgba(201, 162, 51, 0.07);
    --text-light: #ecebe8;
    --divider: #bdbdbd;
  }
  html, body {
    margin: 0;
    padding: 0;
    width: 1200px;
    height: 800px;
    overflow: hidden;
    background: var(--page-bg);
  }
  .business-card {
    position: absolute;
    left: 100px;
    top: 115px;
    width: 1000px;
    height: 570px;
    background: var(--card-bg);
    overflow: hidden;
    font-family: "Poppins", sans-serif;
  }
  .lily-watermark {
    position: absolute;
    left: 400px;
    top: 30px;
    width: 560px;
    height: 520px;
    border-radius: 50%;
    background: radial-gradient(ellipse at center, var(--gold-soft) 0%, rgba(201,162,51,0.03) 55%, rgba(201,162,51,0) 75%);
  }
  .brand-name {
    position: absolute;
    left: 95px;
    top: 258px;
    width: 320px;
    text-align: center;
    color: var(--gold);
    font-weight: 500;
    font-size: 22px;
    letter-spacing: 0.5px;
    line-height: 1.3;
  }
  .brand-name .brand-dot {
    display: inline-block;
    width: 14px;
    height: 14px;
    border-radius: 50%;
    background: var(--gold);
    margin-right: 10px;
    vertical-align: 1px;
  }
  .divider {
    position: absolute;
    left: 449px;
    top: 173px;
    width: 1.5px;
    height: 217px;
    background: var(--divider);
  }
  .contact-block {
    position: absolute;
    left: 479px;
    top: 160px;
    color: var(--text-light);
  }
  .person-name {
    margin: 0 0 18px;
    font-family: "Dancing Script", cursive;
    font-weight: 700;
    font-size: 44px;
    color: var(--gold);
    line-height: 1.1;
  }
  .address {
    margin: 0 0 12px;
    font-size: 22px;
    line-height: 28px;
  }
  .contact-list {
    list-style: none;
    margin: 0;
    padding: 0;
    font-size: 22px;
    line-height: 28px;
  }
  .contact-list li {
    display: flex;
    align-items: center;
  }
  .contact-icon {
    width: 20px;
    height: 20px;
    margin-right: 14px;
    fill: var(--gold);
    flex: none;
  }
</style>
</head>
<body>
  <div class="business-card">
    <div class="lily-watermark" role="img" aria-label="Faint lily decoration behind the contact details"></div>

    <div class="brand-name"><span class="brand-dot"></span>Cove Medical Spa &amp; Wellness</div>

    <div class="divider"></div>

    <div class="contact-block">
      <h1 class="person-name">Daniel Hartwell</h1>
      <p class="address">4820 W. Linden Road, Suite 14<br>Glendale, AZ 85310</p>
      <ul class="contact-list">
        <li>
          <svg class="contact-icon" viewBox="0 0 24 24" aria-hidden="true"><path d="M6.6 10.8c1.4 2.8 3.8 5.1 6.6 6.6l2.2-2.2c.3-.3.7-.4 1-.2 1.1.4 2.3.6 3.6.6.6 0 1 .4 1 1V20c0 .6-.4 1-1 1C10.6 21 3 13.4 3 4c0-.6.4-1 1-1h3.5c.6 0 1 .4 1 1 0 1.3.2 2.5.6 3.6.1.3 0 .7-.2 1l-2.3 2.2z"/></svg>
          (602) 555-0147
        </li>
        <li>
          <svg class="contact-icon" viewBox="0 0 24 24" aria-hidden="true"><path d="M3 5h18v14H3V5zm2 2v.5l7 4.5 7-4.5V7H5zm0 2.9V17h14V9.9l-7 4.5-7-4.5z"/></svg>
          welcome@covewellnessandspa.com
        </li>
        <li>
          <svg class="contact-icon" viewBox="0 0 24 24" aria-hidden="true"><path d="M12 2a10 10 0 1 0 0 20 10 10 0 0 0 0-20zm-1 17.9A8 8 0 0 1 4.1 11H7c0 3 1.5 6 4 8.9zM13 19.9c2.5-2.9 4-5.9 4-8.9h2.9a8 8 0 0 1-6.9 8.9zM9 11h6c0 2.4-1 4.8-3 7.1-2-2.3-3-4.7-3-7.1zm0-2c.3-2 1.3-4 3-6 1.7 2 2.7 4 3 6H9zM4.1 9A8 8 0 0 1 11 4.1C9.5 5.9 8.6 7.5 8.2 9H4.1zm15.8 0h-4.1c-.4-1.5-1.3-3.1-2.8-4.9A8 8 0 0 1 19.9 9z"/></svg>
          www.covewellnessandspa.com
        </li>
      </ul>
    </div>
  </div>
</body>
</html>
```